Natural Supplement Co Needs Label Makeover

Our company's success began with our main product, an amino acid blend that aids in fat metabolism, called Vantorel. Since then we continue to expand the product line that now includes a detox called Vantopurge, and probiotic called Vantoflora, as well as 3 others, for a total of 6 products/ labels.
Our original design/logo had more of an 'old-timey' feel (see attached 2-product photo). We are looking for a fresh label design update for the product line which reflects the range of supplements as cohesive and individual parts of an overall health plan/strategy (see attached 'Logo Update Test' as just one idea we had in-house, you need not consider it as a starting point).

Target Market(s)

women 25-45

Industry/Entity Type

Health And Wellness

Requirements
Must have
• consistent theme with confident look
Nice to have
• Each product (ie. "Vantorel") has a few-word descriptor: ("Fat-Burning Amino Acids") that should be planned on including as part of each label.
Should not have
• NO 'streamlined' or graphic interpretations of the human body, or figurative image

```html
<!DOCTYPE html>
<html lang="en">
<head>
<meta charset="utf-8">
<title>Vantopurge Label</title>
<link rel="stylesheet" href="https://fonts.googleapis.com/css2?family=Roboto+Condensed:wght@400;700&family=Rokkitt:wght@400;500;600&display=swap">
<style>
  :root {
    --backdrop: #eeeeee;
    --label-white: #ffffff;
    --panel-blue: #2b73b8;
    --panel-blue-light: #3a86c9;
    --panel-blue-dark: #1f5f9f;
    --band-yellow: #e8e63a;
    --band-black: #0c0c0c;
    --ink-dark: #2a2a2a;
    --ink-white: #ffffff;
    --ink-grey: #8a8a8a;
    --rule-white: rgba(255, 255, 255, 0.85);
  }
  * { box-sizing: border-box; margin: 0; padding: 0; }
  html, body {
    width: 960px;
    height: 1200px;
    overflow: hidden;
    background: var(--backdrop);
  }
  .canvas {
    position: relative;
    width: 960px;
    height: 1200px;
  }
  .label {
    position: absolute;
    left: 130px;
    top: 76px;
    width: 700px;
    height: 1048px;
    background: var(--label-white);
    box-shadow: 0 2px 12px rgba(0, 0, 0, 0.08);
  }
  .label__panel {
    position: absolute;
    left: 50px;
    right: 50px;
    top: 0;
    height: 763px;
    background: linear-gradient(100deg, var(--panel-blue-dark) 0%, var(--panel-blue) 35%, var(--panel-blue-light) 70%, var(--panel-blue) 100%);
  }
  .label__descriptor-band {
    position: absolute;
    left: 0;
    right: 0;
    top: 105px;
    height: 157px;
    background: var(--band-yellow);
    display: flex;
    align-items: center;
    justify-content: center;
  }
  .label__descriptor {
    font-family: "Rokkitt", serif;
    font-weight: 500;
    font-size: 76px;
    color: var(--ink-dark);
    letter-spacing: 0.5px;
  }
  .label__product-name {
    position: absolute;
    left: 0;
    right: 0;
    top: 355px;
    text-align: center;
    font-family: "Roboto Condensed", sans-serif;
    font-weight: 700;
    font-size: 124px;
    line-height: 1;
    color: var(--ink-white);
    letter-spacing: -1px;
  }
  .label__rule {
    position: absolute;
    left: 86px;
    right: 86px;
    height: 2px;
    background: var(--rule-white);
  }
  .label__rule--top { top: 574px; }
  .label__rule--bottom { top: 699px; }
  .label__formula {
    position: absolute;
    left: 0;
    right: 0;
    top: 604px;
    text-align: center;
    font-family: "Rokkitt", serif;
    font-weight: 500;
    font-size: 60px;
    line-height: 1.3;
    color: var(--ink-white);
    letter-spacing: 1px;
  }
  .label__claim-band {
    position: absolute;
    left: 0;
    right: 0;
    top: 763px;
    height: 90px;
    background: var(--band-black);
    display: flex;
    align-items: center;
    justify-content: center;
  }
  .label__claim {
    font-family: "Rokkitt", serif;
    font-weight: 600;
    font-size: 46px;
    color: var(--ink-white);
    letter-spacing: 0.5px;
  }
  .label__volume {
    position: absolute;
    left: 0;
    right: 0;
    top: 940px;
    text-align: center;
    font-family: "Roboto Condensed", sans-serif;
    font-weight: 400;
    font-size: 34px;
    color: var(--ink-grey);
  }
</style>
</head>
<body>
  <main class="canvas">
    <section class="label">
      <div class="label__panel"></div>
      <div class="label__descriptor-band">
        <span class="label__descriptor">Fat Burning</span>
      </div>
      <h1 class="label__product-name">Vantopurge</h1>
      <div class="label__rule label__rule--top"></div>
      <p class="label__formula">AMINO ACIDS</p>
      <div class="label__rule label__rule--bottom"></div>
      <div class="label__claim-band">
        <span class="label__claim">ALL NATURAL SUPPLEMENT</span>
      </div>
      <p class="label__volume">1 FL. OZ (30 ml)</p>
    </section>
  </main>
</body>
</html>
```